Web Design job: SaaS start-up needs a cutting-edge web design

What's Needed:
- All designs files created
- Fully coded implementation in HTML/CSS/Bootstrap
- Pages: 5 -- see content here http://www.TeamVerdexa.com
-- Home Page
-- The Hidden Value
-- Benefits
-- About us
-- Careers
- The existing site has the textual content for each page. We can tweak to meet specific designs if needed.
- You will need to update/create image and interactive content for pages.

Reference:
Our existing website has a lot of content on it for reference -
http://www.TeamVerdexa.com

Description:
We need a web design that focuses in the UX and conveys the idea of magically fixing company problems by way of using our software.

Home Page
The main goal is to Drive Sales of the SaaS tool. When a visitor lands on our home page they should see: What we do, How we can help their problem and How to contact us.
1. Quickly understand What We Do
-- we sell SaaS software.
-- Need to quickly convey what our software does. It's seems complicated but really its not. See the description in about us for more info and visit our existing site.

2. How we can help their problem
-- We aim to solve any problem related to employees
-- Even if the visitor does not have a specific problem in mind, there are several areas organizations can always improve: (some examples below)
---- Create Stronger, More Productive Teams
---- Build Better Communications Pathways
---- Encourage Innovation and Positive Change
---- Develop and Retain Strong "Company Culture"

3. Be able to Contact Us to get started
-- contacting us to get a sales lead is the ultimate goal.
-- the user should not have to hunt to contact us. needs to be easy.

Other Pages (Hidden Value, Benefit, About Us, Careers):
-- These are informative pages about our software and process.
-- If we grab the attention of the user on the home page then these are the pages that they will explore for more info.
-- Should be able to link to these pages from the main nav or from sections with the homepage. For example: What We Do sections could link to the benefits page. How we help their problem sections could link to the Hidden Value page. Regardless of what links to where, the idea is that we will be able to nav to other areas.

About Us:
Our company name is TeamVerdexa (as in Organizational Analysis). We provide a software as a service (SaaS) that uses a simple 6-question survey to analyze the relationships of people within an Organization and provide leaders with ground-breaking Insights about their teams, interactive social network data visualizations to explore their team's composition and we give detailed profiles of the key players (i.e, who are the Social Bridges, Who are the Knowledge Bottlenecks, Who are the Best Mentors, Who are the people that are completely disconnected/out of the loop). Leaders then use this information to make high level organizational decisions.

What's unique about our software:
-- Powerful analysis results from just a 6-question "pulse-surveys"
-- Innovative Tools for visually exploring the organization through relationships as opposed to org-chart
-- Get real-time results as opposed to waiting months with traditional methods
-- Traditional Org-charts represent the organization's skeleton, whereas we uncover the organization's neural network (how it solves problems).

Preferred fonts (but could be convinced otherwise if looks great):
-- Section titles - Aleo
-- Main body - Lato
-- TeamVerdexa logo - Philosopher

Things we like:
-- We like a big slider as the top of the landing page.

Colors to include:
-- Colors in the logo (red, blue, green, teal) as accent colors

Feel of the site:
-- Cutting-edge Software
-- Professional
-- Social Network flare (we analyze relationships)

Note:
If we find a great match with a designer there is strong possibility to continue the relationship with follow on work redesigning our web-based application.

Target Market(s)

Current customers are Morrow Pike & Fenwell, Clearbrook Valley Bank.
We target anyone that manages a large team. Such as Corporate Leaders, High Level Managers, HR Leaders

Industry/Entity Type

Business Software

Contact Information for Business Card

Logo image
Name of company "TEAMVERDEXA" In Philosopher font.
Tagline: "Unlock the Hidden Value In Your Teams"
Person's Name, Title, email, phone.

Coding

Coded - Design and coding required

Number of Pages Required

4 page

Font styles to use
Other font styles liked:
• Lato, Philosopher, Aero

Colors
ec1f27
0255a3

Requirements
Must have
• See description.
Nice to have
• Things we like:
• We like a big slider as the top of the landing page. Ours is a little clunky and outdated but something fresh and sleek would be great.
• Colors to include:
• We would like to use the colors in the logo as accent colors in the site to give a consistent look and feel.
• Feel of the site:
• Cutting-edge Software
• Professional
• Social Network flare (we analyze relationships)

```html
<!DOCTYPE html>
<html lang="en">
<head>
<meta charset="utf-8">
<title>TeamVerdexa — World-Class Analytics</title>
<link rel="stylesheet" href="https://fonts.googleapis.com/css2?family=Lato:wght@300;400;700&display=swap">
<style>
:root{
  --brand:#0a4f9e;
  --ink:#333;
  --ink-soft:#555;
  --muted:#888;
  --band:#f3f3f3;
  --line:#dedede;
  --white:#fff;
  --arrow:#d6d6d6;
}
*{box-sizing:border-box;margin:0;padding:0}
html,body{width:1200px;height:2635px;overflow:hidden;background:var(--white)}
body{position:relative;font-family:'Lato',sans-serif;color:var(--ink)}
.abs{position:absolute}

.site-header{position:absolute;left:0;top:0;width:1200px;height:100px;background:var(--white);border-top:3px solid var(--brand);box-shadow:0 2px 6px rgba(0,0,0,.12);z-index:2}
.logo{position:absolute;left:130px;top:22px;display:flex;flex-direction:column;align-items:center;gap:6px}
.logo-mark{width:30px;height:30px;border-radius:50%;background:var(--brand)}
.logo-name{font-size:15px;font-weight:700;letter-spacing:1px;color:var(--brand)}
.main-nav{position:absolute;left:620px;top:0;display:flex}
.nav-item{height:97px;display:flex;flex-direction:column;align-items:center;justify-content:center;gap:14px;font-size:11px;color:var(--ink);padding:0 22px;letter-spacing:.3px}
.nav-item svg{width:12px;height:12px;fill:var(--ink)}
.nav-item.is-active{color:var(--brand);border-bottom:3px solid var(--brand)}
.nav-item.is-active svg{fill:var(--brand)}

.hero{position:absolute;left:0;top:100px;width:1200px;height:476px;background:var(--band)}
.hero-visual{position:absolute;left:175px;top:10px;width:415px;height:440px;border-radius:50%;background:radial-gradient(circle at 45% 40%,#d94a7a 0%,#9a6fd6 40%,#4b74d0 65%,rgba(243,243,243,0) 72%)}
.hero-title{position:absolute;left:658px;top:55px;font-size:58px;line-height:68px;font-weight:300;color:var(--ink)}
.hero-title strong{font-weight:700;display:block}
.hero-copy{position:absolute;left:658px;top:222px;width:330px;font-size:13px;line-height:22px;color:var(--ink)}
.btn{display:inline-flex;align-items:center;justify-content:center;background:var(--brand);color:var(--white);font-size:13px;border-radius:2px}
.hero-cta{position:absolute;left:656px;top:295px;width:140px;height:50px}
.slider-arrow{position:absolute;top:193px;width:45px;height:45px;background:var(--arrow);display:flex;align-items:center;justify-content:center}
.slider-arrow svg{width:14px;height:14px;stroke:var(--white);fill:none;stroke-width:2}

.section-title{position:absolute;left:0;width:1200px;text-align:center;font-size:34px;font-weight:300;color:var(--ink)}
.service{position:absolute;width:220px;text-align:center}
.service-icon{height:165px;display:flex;align-items:flex-end;justify-content:center}
.service-label{margin-top:35px;font-size:18px;font-weight:300;line-height:23px;color:var(--ink-soft)}

.help{position:absolute;left:0;top:1048px;width:1200px;height:1135px;background:var(--band)}
.timeline-line{position:absolute;left:596px;top:160px;width:9px;height:882px;background:var(--white);border:1px solid var(--line)}
.help-card{position:absolute;width:376px;height:125px;background:var(--white);border:1px solid var(--line);display:flex;align-items:flex-start;padding:28px 20px 0 30px;gap:22px}
.help-card svg{flex:none;width:40px;height:40px;stroke:var(--brand);fill:none;stroke-width:1.6}
.help-card p{font-size:18px;font-weight:300;line-height:29px;color:var(--ink)}

.contact-field{position:absolute;border:1px solid var(--line);border-radius:2px;font-size:11px;color:var(--ink-soft);padding:12px 14px}
.contact-submit{position:absolute;left:153px;top:2505px;width:108px;height:36px}
.info-row{position:absolute;display:flex;gap:14px;font-size:10px;line-height:14px;color:var(--ink-soft)}
.info-row svg{flex:none;width:11px;height:11px;fill:var(--ink-soft)}
.social{position:absolute;left:668px;top:2390px;display:flex;gap:7px}
.social span{width:33px;height:33px;border:1.5px solid var(--ink-soft);border-radius:50%}
.footer-rule{position:absolute;left:133px;top:2565px;width:934px;height:1px;background:var(--line)}
.copyright{position:absolute;left:0;top:2589px;width:1200px;text-align:center;font-size:10px;color:var(--ink)}
</style>
</head>
<body>

<header class="site-header">
  <div class="logo"><span class="logo-mark"></span><span class="logo-name">TEAMVERDEXA</span></div>
  <nav class="main-nav">
    <div class="nav-item is-active"><svg viewBox="0 0 12 12"><path d="M6 1 0 6h2v5h3V8h2v3h3V6h2z"/></svg>HOME</div>
    <div class="nav-item"><svg viewBox="0 0 12 12"><circle cx="6" cy="3.5" r="2.8"/><path d="M1 12c0-4 2-5.5 5-5.5s5 1.5 5 5.5z"/></svg>ABOUT US</div>
    <div class="nav-item"><svg viewBox="0 0 12 12"><path d="M4 3 1 6l3 3M8 3l3 3-3 3" stroke="#333" fill="none" stroke-width="1.3"/></svg>SERVICES</div>
    <div class="nav-item"><svg viewBox="0 0 12 12"><rect x="0" y="2" width="12" height="8" rx="1"/></svg>NEWS</div>
    <div class="nav-item"><svg viewBox="0 0 12 12"><path d="M6 0a4 4 0 0 0-4 4c0 3 4 8 4 8s4-5 4-8a4 4 0 0 0-4-4z"/></svg>CONTACT US</div>
  </nav>
</header>

<section class="hero">
  <div class="hero-visual" role="img" aria-label="Colourful social network graph of connected people"></div>
  <h1 class="hero-title">World-Class <strong>Analytics</strong></h1>
  <p class="hero-copy">Nemo enim ipsam voluptatem quia voluptas sit aspernatur aut odit aut fugit,</p>
  <a class="btn hero-cta">VIEW DETAILS</a>
  <div class="slider-arrow" style="left:47px"><svg viewBox="0 0 14 14"><path d="M9 2 4 7l5 5"/></svg></div>
  <div class="slider-arrow" style="left:1103px"><svg viewBox="0 0 14 14"><path d="M5 2l5 5-5 5"/></svg></div>
</section>

<h2 class="section-title" style="top:615px">What we do</h2>
<div class="service" style="left:93px;top:705px">
  <div class="service-icon"><div role="img" aria-label="Clipboard survey icon" style="width:130px;height:160px;background:var(--brand);border-radius:6px"></div></div>
  <p class="service-label">Online Pulse<br>Survey</p>
</div>
<div class="service" style="left:358px;top:705px">
  <div class="service-icon"><div role="img" aria-label="Laptop with check mark icon" style="width:205px;height:155px;background:#3d3d3d;border-radius:6px"></div></div>
  <p class="service-label">Proprietary<br>Algorithms</p>
</div>
<div class="service" style="left:647px;top:705px">
  <div class="service-icon">
    <svg width="170" height="160" viewBox="0 0 170 160" fill="none" stroke="#3d3d3d" stroke-width="9">
      <rect x="60" y="5" width="50" height="35"/><path d="M85 40v40M25 80h120M25 80v38M85 80v38M145 80v38"/>
      <rect x="5" y="118" width="40" height="37"/><rect x="65" y="118" width="40" height="37"/><rect x="125" y="118" width="40" height="37"/>
    </svg>
  </div>
  <p class="service-label">Organizational Key<br>Insights</p>
</div>
<div class="service" style="left:897px;top:705px">
  <div class="service-icon"><div role="img" aria-label="Expert reviewer figure icon" style="width:120px;height:165px;background:#3d3d3d;border-radius:50px 50px 6px 6px"></div></div>
  <p class="service-label">Expert Review<br>and Plans</p>
</div>

<section class="help">
  <h2 class="section-title" style="top:56px">How we can help</h2>
  <div class="timeline-line"></div>
  <div class="help-card" style="left:199px;top:145px"><svg viewBox="0 0 40 40"><rect x="4" y="8" width="32" height="26"/><path d="M16 4h8v6h-8zM9 16h9v10H9zM22 18h9M22 23h9"/></svg><p>We aim to solve any problem related to employees</p></div>
  <div class="help-card" style="left:623px;top:305px"><svg viewBox="0 0 40 40"><rect x="4" y="4" width="32" height="32"/><circle cx="20" cy="20" r="8"/><circle cx="20" cy="20" r="2"/></svg><p>Even if the visitor does not have a specific problem in mind</p></div>
  <div class="help-card" style="left:199px;top:465px"><svg viewBox="0 0 40 40"><circle cx="15" cy="14" r="6"/><path d="M4 33c0-8 5-11 11-11s11 3 11 11z"/><path d="M22 9a6 6 0 1 1 3 11M28 22c5 1 8 4 8 11h-8"/></svg><p>Create Stronger, More Productive Teams</p></div>
  <div class="help-card" style="left:623px;top:616px"><svg viewBox="0 0 40 40"><path d="M6 15h26l-6-6M34 25H8l6 6"/></svg><p>Build Better Communications Pathways</p></div>
  <div class="help-card" style="left:199px;top:762px"><svg viewBox="0 0 40 40"><path d="M4 18h7v17H4zM11 20l8-14c3 0 4 2 3 6l-2 5h13c2 0 3 2 2 4l-3 11c-1 2-2 3-4 3H11"/></svg><p>Encourage Innovation and Positive Change</p></div>
  <div class="help-card" style="left:623px;top:905px"><svg viewBox="0 0 40 40"><rect x="4" y="11" width="32" height="23"/><path d="M14 11V6h12v5M4 20h32M18 18h4v5h-4z"/></svg><p>Develop and Retain Strong "Company Culture"</p></div>
</section>

<h2 class="section-title" style="top:2210px">Contact Us</h2>
<div class="contact-field" style="left:153px;top:2285px;width:242px;height:42px">Name</div>
<div class="contact-field" style="left:406px;top:2285px;width:244px;height:42px">Email</div>
<div class="contact-field" style="left:153px;top:2340px;width:497px;height:148px">Message</div>
<a class="btn contact-submit">Submit</a>

<div class="info-row" style="left:668px;top:2285px"><svg viewBox="0 0 11 11"><path d="M1 1h9v3H1zM2 5h7v5H2z"/></svg>555-014-2231</div>
<div class="info-row" style="left:668px;top:2310px"><svg viewBox="0 0 11 11"><rect y="2" width="11" height="7"/></svg>east@teamverdexa.com</div>
<div class="info-row" style="left:668px;top:2335px"><svg viewBox="0 0 11 11"><path d="M5.5 0a3.5 3.5 0 0 0-3.5 3.5C2 6 5.5 11 5.5 11S9 6 9 3.5A3.5 3.5 0 0 0 5.5 0z"/></svg>#2868 Lorem ipsum dolor sit<br>amet, consectetur</div>
<div class="info-row" style="left:860px;top:2285px"><svg viewBox="0 0 11 11"><path d="M1 1h9v3H1zM2 5h7v5H2z"/></svg>555-019-7720</div>
<div class="info-row" style="left:860px;top:2310px"><svg viewBox="0 0 11 11"><rect y="2" width="11" height="7"/></svg>west@teamverdexa.com</div>
<div class="info-row" style="left:860px;top:2335px"><svg viewBox="0 0 11 11"><path d="M5.5 0a3.5 3.5 0 0 0-3.5 3.5C2 6 5.5 11 5.5 11S9 6 9 3.5A3.5 3.5 0 0 0 5.5 0z"/></svg>#2868 Lorem ipsum dolor sit<br>amet, consectetur</div>
<div class="social"><span></span><span></span><span></span><span></span><span></span></div>

<div class="footer-rule"></div>
<p class="copyright">© 2016 TeamVerdexa. All Rights Reserved.</p>

</body>
</html>
```